Modern Business Card For A Digital Advertising Company

I'll be print on the Pell Prints Velour paper http://us.pellprints.com/products/velour/business-cards.html
Need's to be modern and use the color palette of the logo or gray scales. I think integrating the pixelation of the logo in to the card and having it wrap from one side to the other could be interesting. My company provides ad operations, web development, and number of other services to websites around the world. You can see my website at http://www.zantorhq.com
Contact info on the card needs to have
Owen Lasko
President
p.318.204.6637
owen@zantorhq.com
http://www.zantorhq.com
Doesn't necessarily need to be in that order
Website owners
Business

```html
<!DOCTYPE html>
<html lang="en">
<head>
<meta charset="utf-8">
<title>Zantor HQ — Business Card</title>
<link rel="stylesheet" href="https://fonts.googleapis.com/css2?family=Source+Sans+3:wght@400;600&display=swap">
<style>
  :root{
    --backdrop:#4b2a1b;
    --card:#ffffff;
    --green:#8cc63f;
    --charcoal:#4a4a48;
    --ink:#3a3a3a;
    --muted:#6b6b6b;
  }
  html,body{margin:0;padding:0;overflow:hidden;}
  body{width:1200px;height:448px;background:var(--backdrop);position:relative;
       font-family:"Source Sans 3",Arial,sans-serif;}
  .card{position:absolute;background:var(--card);border-radius:22px;overflow:hidden;
        box-shadow:0 3px 8px rgba(0,0,0,.35);}
  .card--front{left:82px;top:68px;width:508px;height:320px;}
  .card--back{left:615px;top:72px;width:510px;height:290px;}
  .swoosh{position:absolute;left:0;top:0;}
  .brand{position:absolute;margin:0;color:var(--green);font-weight:600;
         letter-spacing:1px;line-height:1;}
  .card--front .brand{left:52px;top:156px;font-size:36px;}
  .brand-mark{position:absolute;background:var(--green);}
  .card--front .brand-mark{left:52px;top:40px;width:96px;height:96px;}
  .contact{position:absolute;right:28px;top:176px;margin:0;padding:0;list-style:none;
           font-size:13px;color:var(--ink);text-align:right;}
  .contact li{height:20px;line-height:20px;margin-bottom:1px;display:flex;
              justify-content:flex-end;align-items:center;gap:8px;}
  .contact .icon{width:9px;height:9px;border-radius:50%;background:var(--green);flex:none;}
  .identity{position:absolute;right:26px;top:242px;display:flex;align-items:center;gap:8px;}
  .identity .name{color:var(--green);font-size:19px;font-weight:600;}
  .identity .rule{width:1px;height:18px;background:#9a9a9a;}
  .identity .role{color:var(--muted);font-size:12.5px;}
  .card--back .brand-mark{left:183px;top:71px;width:62px;height:62px;}
  .card--back .brand{left:0;right:0;top:142px;text-align:center;font-size:30px;}
  .card--back .web{position:absolute;left:0;right:0;top:202px;text-align:center;
                   font-size:13px;letter-spacing:2.4px;color:var(--ink);}
</style>
</head>
<body>
  <section class="card card--front" aria-label="Card front">
    <svg class="swoosh" width="508" height="320" viewBox="0 0 508 320" aria-hidden="true">
      <path d="M330 0 C420 6 480 40 508 88 L508 60 C485 25 430 2 360 0 Z" fill="var(--charcoal)"/>
      <path d="M300 0 C410 4 478 30 508 70 L508 0 Z" fill="var(--green)"/>
      <path d="M0 212 C30 262 100 300 200 320 L150 320 C80 300 28 268 0 238 Z" fill="var(--charcoal)"/>
      <path d="M0 238 C40 280 110 308 190 320 L0 320 Z" fill="var(--green)"/>
    </svg>
    <div class="brand-mark" aria-hidden="true"></div>
    <p class="brand">ZANTOR HQ</p>
    <ul class="contact">
      <li>318.204.6637<span class="icon"></span></li>
      <li>owen@zantorhq.com<span class="icon"></span></li>
      <li>http://www.zantorhq.com<span class="icon"></span></li>
    </ul>
    <div class="identity">
      <span class="name">Owen Lasko</span><span class="rule"></span><span class="role">President</span>
    </div>
  </section>

  <section class="card card--back" aria-label="Card back">
    <div class="brand-mark" aria-hidden="true"></div>
    <p class="brand">ZANTOR HQ</p>
    <p class="web">www.zantorhq.com</p>
  </section>
</body>
</html>
```